co working space / serviced office/ business centre

Brevlo - brevlo.in, is a very young brand bieng run by 3 young entrepreneurs. We want to be become out of the league company delivering fabulous and beautiful serviced offices in India and abroad. We hire designers who have made spaces across the world. We want to get visiting card design which gives complete fresh look to the people who carries that card, has to be very impactful and should symbolise happy young and energetic brand. should be completely out of the box thinking of international level, should portray global brand image.

Target Market(s)

Startups, (Small, medium and large corporates)

Industry/Entity Type

Business

Contact Information for Business Card

Name, Email, Address, Mobile number, Landline number, website

Colors

Designer to choose colors to be used in the design.

Requirements
Must have
• Nice new shape
Nice to have
• We want creative cuts, different size and impactful brand clarity
Should not have
• Boring and regular design and shape

```html
<!DOCTYPE html>
<html lang="en">
<head>
<meta charset="UTF-8">
<title>Brevlo – Business Card</title>
<link href="https://fonts.googleapis.com/css2?family=Michroma&family=Lato:wght@400;700;900&display=swap" rel="stylesheet">
<style>
  :root {
    --brand-red: #e8262b;
    --card-white: #ffffff;
    --card-dark: #1f1f20;
    --text-light: #ffffff;
    --backdrop: #d8d2cb;
  }
  * { margin: 0; padding: 0; box-sizing: border-box; }
  html, body { width: 1200px; height: 675px; overflow: hidden; }
  body { background: var(--backdrop); position: relative; font-family: "Lato", sans-serif; }

  .card {
    position: absolute;
    border-radius: 999px;
    box-shadow: 0 6px 14px rgba(0,0,0,0.28);
  }
  .card__frame {
    position: absolute;
    inset: 8px;
    border-radius: 999px;
    border: 3px solid var(--brand-red);
  }

  /* Front */
  .card--front { left: 83px; top: 80px; width: 520px; height: 288px; background: var(--card-white); }
  .brand-name {
    position: absolute; left: 0; right: 0; top: 122px;
    text-align: center; color: var(--brand-red);
    font-family: "Lato", sans-serif; font-weight: 900;
    font-size: 58px; line-height: 66px; letter-spacing: 6px;
  }
  .brand-rule {
    position: absolute; left: 117px; width: 294px; top: 196px;
    height: 3px; background: var(--brand-red);
  }
  .brand-tagline {
    position: absolute; left: 0; right: 0; top: 213px;
    text-align: center; color: var(--brand-red);
    font-family: "Michroma", sans-serif; font-size: 12px; letter-spacing: 2px;
  }

  /* Back */
  .card--back { left: 537px; top: 305px; width: 520px; height: 285px; background: var(--card-dark); }
  .card--back .card__frame { inset: 6px; }
  .back-brand {
    position: absolute; left: 0; right: 0; top: 66px;
    text-align: center; color: var(--brand-red);
    font-family: "Lato", sans-serif; font-weight: 900;
    font-size: 28px; line-height: 32px; letter-spacing: 4px;
  }
  .holder-name {
    position: absolute; left: 0; right: 0; top: 134px;
    text-align: center; color: var(--brand-red);
    font-family: "Michroma", sans-serif; font-size: 17px; line-height: 22px; letter-spacing: 1px;
  }
  .holder-rule {
    position: absolute; left: 172px; width: 184px; top: 161px;
    height: 2px; background: var(--brand-red);
  }
  .holder-role {
    position: absolute; left: 0; right: 0; top: 169px;
    text-align: center; color: var(--brand-red);
    font-family: "Michroma", sans-serif; font-size: 10.5px; letter-spacing: 1.5px;
  }
  .contact {
    position: absolute; left: 0; right: 0; top: 197px;
    text-align: center; color: var(--text-light);
    font-size: 13px; line-height: 18px; font-style: normal;
  }
  .contact__label { color: var(--brand-red); font-weight: 700; }
</style>
</head>
<body>
  <section class="card card--front" aria-label="Card front">
    <div class="card__frame"></div>
    <h1 class="brand-name">BREVLO</h1>
    <div class="brand-rule"></div>
    <p class="brand-tagline">MEET. PLAN. GROW</p>
  </section>

  <section class="card card--back" aria-label="Card back">
    <div class="card__frame"></div>
    <p class="back-brand">BREVLO</p>
    <h2 class="holder-name">ARJUN MEHRA</h2>
    <div class="holder-rule"></div>
    <p class="holder-role">CEO/FOUNDER</p>
    <address class="contact">
      Tower 4C, Park Avenue, Noida<br>
      <span class="contact__label">P</span>: +91 8400123456 <span class="contact__label">C</span>: +91 9800765432<br>
      <span class="contact__label">E</span>: arjun@brevlo.in <span class="contact__label">W</span>: www.brevlo.in
    </address>
  </section>
</body>
</html>
```